Business card design for Automotive workshop

We need a business card for a new automotive repair and tyre shop called Keelstone Prime Automotive located in New Zealand. We are a clean, modern and fresh workshop and company.

Front needs to feature logo,
my name:
Marlo Fenwicke (director)

Address:
48 Tarn Lane
Kauriwai 3594

Phone: 07 594 2713
Mobile: 027 451 9362
Email: office@keelstoneautomotive.example.nz
Website: keelstoneautomotive.example.nz

Back needs to feature an area to write down appointment details, date and time.

Also feature a list of jobs and work we do such as,
Vehicle Servicing
All Mechanical Repairs
Warrant of Fitness
Tyres & Wheel Alignments
Automotive Diagnostics
Automotive Parts & Supplies

```html
<!DOCTYPE html>
<html lang="en">
<head>
<meta charset="utf-8">
<title>Keelstone Prime Automotive – Business Card</title>
<link rel="stylesheet" href="https://fonts.googleapis.com/css2?family=Open+Sans:wght@400;600;700&family=Roboto:wght@400;500;700&display=swap">
<style>
  :root {
    --red: #e31e2d;
    --black: #1a1a1a;
    --card-dark: #202020;
    --ink: #3a3a3a;
    --grey: #6b6b6b;
    --paper: #ffffff;
    --bg: #dcdcdc;
  }
  * { box-sizing: border-box; margin: 0; padding: 0; }
  html, body { width: 1200px; height: 960px; overflow: hidden; }
  body {
    background: var(--bg);
    font-family: "Open Sans", Arial, sans-serif;
    position: relative;
  }
  .card {
    position: absolute;
    left: 250px;
    width: 700px;
    height: 400px;
    overflow: hidden;
    box-shadow: 0 6px 18px rgba(0,0,0,.18);
  }

  /* Back side */
  .card-back { top: 40px; background: var(--card-dark); color: #fff; }
  .back-brand {
    position: absolute; top: 36px; left: 0; right: 0;
    text-align: center;
    font-size: 34px; font-weight: 700; letter-spacing: 1px;
    color: #e8e8e8;
  }
  .services {
    position: absolute; top: 104px; left: 0; right: 0;
    text-align: center;
    font-family: "Roboto", Arial, sans-serif;
  }
  .services-title {
    color: var(--red); font-weight: 700; font-size: 19px;
    margin-bottom: 6px;
  }
  .services-list { font-size: 15px; line-height: 1.45; color: #f2f2f2; }
  .services-list .dot { color: var(--red); margin: 0 6px; }
  .appointment {
    position: absolute; left: 30px; right: 30px; bottom: 30px;
    height: 118px; background: var(--paper);
    padding: 22px 26px;
    font-family: "Roboto", Arial, sans-serif;
  }
  .appointment-row {
    display: flex; align-items: flex-end; gap: 8px;
    height: 38px;
    color: var(--red); font-size: 15px; font-weight: 500;
  }
  .fill-line { flex: 1; border-bottom: 2px dotted #777; margin-bottom: 4px; }
  .fill-line.date { flex: 1.3; }

  /* Front side */
  .card-front { top: 500px; background: var(--paper); }
  .front-brand {
    position: absolute; top: 62px; right: 48px;
    display: flex; align-items: center; gap: 10px;
    font-size: 28px; font-weight: 700; color: var(--red);
  }
  .brand-square { width: 18px; height: 18px; background: var(--black); }
  .person-name {
    position: absolute; left: 40px; top: 172px;
    font-size: 26px; font-weight: 600; color: var(--red); line-height: 1.2;
  }
  .divider {
    position: absolute; left: 40px; right: 50px; top: 212px;
    border-top: 1.5px solid var(--ink);
  }
  .person-role {
    position: absolute; left: 40px; top: 220px;
    font-size: 16px; color: var(--black);
  }
  .contact {
    position: absolute; left: 40px; top: 262px;
    list-style: none; font-size: 17px; color: var(--ink);
  }
  .contact li { display: flex; align-items: center; gap: 10px; height: 26px; }
  .contact svg { width: 14px; height: 14px; fill: var(--red); flex: none; }
  .address {
    position: absolute; right: 50px; top: 224px;
    text-align: right; font-size: 16px; color: var(--grey); line-height: 1.4;
  }
  .website {
    position: absolute; right: 50px; top: 284px;
    font-size: 16px; color: var(--grey);
  }
  .stripe-black { position: absolute; left: 0; right: 0; bottom: 16px; height: 4px; background: var(--black); }
  .stripe-red { position: absolute; left: 0; right: 0; bottom: 0; height: 12px; background: var(--red); }
</style>
</head>
<body>

<section class="card card-back">
  <div class="back-brand">Keelstone Prime Automotive</div>
  <div class="services">
    <div class="services-title">VEHICLE SERVICING</div>
    <div class="services-list">
      All Mechanical Repairs<span class="dot">•</span>Warrant of Fitness<span class="dot">•</span>Tyres &amp; Wheel Alignments<br>
      Automotive Diagnostics<span class="dot">•</span>Automotive Parts &amp; Supplies
    </div>
  </div>
  <div class="appointment">
    <div class="appointment-row"><span>Date:</span><span class="fill-line date"></span><span>Time:</span><span class="fill-line"></span></div>
    <div class="appointment-row"><span>Date:</span><span class="fill-line date"></span><span>Time:</span><span class="fill-line"></span></div>
  </div>
</section>

<section class="card card-front">
  <div class="front-brand"><span class="brand-square"></span>Keelstone Prime Automotive</div>
  <div class="person-name">Marlo Fenwicke</div>
  <div class="divider"></div>
  <div class="person-role">Director</div>
  <ul class="contact">
    <li>
      <svg viewBox="0 0 24 24" aria-hidden="true"><path d="M6.6 10.8a15.1 15.1 0 0 0 6.6 6.6l2.2-2.2a1 1 0 0 1 1-.25 11.4 11.4 0 0 0 3.6.57 1 1 0 0 1 1 1V20a1 1 0 0 1-1 1A17 17 0 0 1 3 4a1 1 0 0 1 1-1h3.5a1 1 0 0 1 1 1c0 1.25.2 2.46.57 3.6a1 1 0 0 1-.25 1z"/></svg>
      07 594 2713
    </li>
    <li>
      <svg viewBox="0 0 24 24" aria-hidden="true"><path d="M7 1h10a2 2 0 0 1 2 2v18a2 2 0 0 1-2 2H7a2 2 0 0 1-2-2V3a2 2 0 0 1 2-2zm0 3v14h10V4zm5 15.2a1 1 0 1 0 0 2 1 1 0 0 0 0-2z"/></svg>
      027 451 9362
    </li>
    <li>
      <svg viewBox="0 0 24 24" aria-hidden="true"><path d="M2 5h20v14H2zm2 2v.5l8 5 8-5V7zm0 2.9V17h16V9.9l-8 5z"/></svg>
      office@keelstoneautomotive.example.nz
    </li>
  </ul>
  <div class="address">48 Tarn Lane<br>Kauriwai 3594</div>
  <div class="website">www.keelstoneautomotive.example.nz</div>
  <div class="stripe-black"></div>
  <div class="stripe-red"></div>
</section>

</body>
</html>
```